Fahrzeugaufbereitung inkl. Hol- und Bringedienst
Zielgruppe
Für Privatkunden
Aufgabenstellung
Benötige einen Flyer, um Privatkunden unseren neuen Hol- und Bringedienst für Fahrzeugaufbereitung vorzustellen.
Text und Preise unter www.belvo-fahrdienst.de unter Fahrzeugaufbereitung.
Format Din Lang (105x210mm), zweiseitig

```html
<!DOCTYPE html>
<html lang="de">
<head>
<meta charset="utf-8">
<title>Belvo Fahrzeugaufbereitung – Flyer DIN lang</title>
<link href="https://fonts.googleapis.com/css2?family=Roboto+Condensed:wght@300;400;700&display=swap" rel="stylesheet">
<style>
  :root {
    --orange: #f08a2c;
    --blue: #3fa9e0;
    --black: #000;
    --white: #fff;
    --photo-dark: #3a3a3a;
    --photo-mid: #6b6b6b;
    --photo-light: #bdbdbd;
    --backdrop: #d6d6d6;
    --font: "Roboto Condensed", "Arial Narrow", sans-serif;
  }
  * { box-sizing: border-box; margin: 0; padding: 0; }
  html, body { width: 1200px; height: 1139px; overflow: hidden; }
  body { background: var(--backdrop); font-family: var(--font); position: relative; }

  .flyer {
    position: absolute; width: 960px; height: 470px;
    background: var(--white); overflow: hidden;
    box-shadow: 0 3px 10px rgba(0,0,0,.25);
  }
  .flyer--front { left: 90px; top: 60px; }
  .flyer--back { left: 150px; top: 610px; }
  .flyer__stripe { position: absolute; left: 0; top: 0; width: 100%; height: 8px; background: var(--orange); }

  .photo { position: absolute; }
  .photo--front {
    left: 530px; top: 8px; width: 430px; height: 462px;
    background: radial-gradient(ellipse at 55% 50%, var(--photo-light) 0%, var(--photo-mid) 35%, var(--photo-dark) 75%);
  }
  .photo--back {
    left: 0; top: 8px; width: 350px; height: 462px;
    background: radial-gradient(ellipse at 40% 50%, var(--photo-light) 0%, var(--photo-mid) 35%, var(--photo-dark) 75%);
  }

  .brand { font-family: var(--font); font-weight: 700; color: var(--blue); letter-spacing: 1px; line-height: 1; }
  .brand--front { position: absolute; left: 38px; top: 55px; font-size: 92px; }
  .brand--back { position: absolute; right: 34px; bottom: 24px; font-size: 50px; }

  .front__panel { position: absolute; left: 0; top: 180px; width: 530px; height: 290px; background: var(--black); padding: 22px 30px 0 30px; color: var(--white); }
  .headline { color: var(--orange); font-weight: 700; line-height: 1; white-space: nowrap; }
  .front__panel .headline { font-size: 50px; }
  .front__sub { font-size: 38px; font-weight: 400; margin-top: 10px; }
  .front__text { font-size: 15px; line-height: 1.45; width: 320px; margin-top: 36px; }
  .front__url { position: absolute; left: 30px; bottom: 22px; font-size: 20px; }

  .badge { position: absolute; width: 150px; height: 150px; }
  .badge svg { position: absolute; inset: 0; }
  .badge__text { position: absolute; inset: 0; color: var(--white); text-align: center; font-family: var(--font); }
  .badge--price { left: 445px; top: 290px; }
  .badge--price .nur { position: absolute; left: 30px; top: 34px; font-size: 20px; }
  .badge--price .price { position: absolute; left: 22px; top: 60px; font-size: 46px; font-weight: 700; }
  .badge--price .price small { font-size: 18px; font-weight: 400; margin-right: 6px; }
  .badge--price .price sup { font-size: 20px; vertical-align: 18px; }
  .badge--new { left: 282px; top: 200px; }
  .badge--new .badge__text { padding-top: 34px; font-weight: 700; font-size: 22px; line-height: 1.2; }
  .badge--new .big { font-size: 34px; display: block; margin-top: 4px; }

  .back__top { position: absolute; left: 350px; top: 8px; width: 610px; height: 165px; background: var(--black); padding: 18px 40px 0 58px; color: var(--white); }
  .back__top .headline { font-size: 56px; }
  .back__intro { font-size: 16px; line-height: 1.35; margin-top: 14px; }

  .services { position: absolute; left: 504px; top: 190px; color: var(--black); font-size: 15px; line-height: 1.3; }
  .services__title { color: var(--orange); font-weight: 700; font-size: 15px; }
  .services ul { list-style: none; }
  .services li::before { content: "· "; }
  .cta { position: absolute; left: 504px; top: 332px; color: var(--orange); font-weight: 700; font-size: 25px; white-space: nowrap; }

  .contact { position: absolute; left: 382px; top: 372px; font-size: 14px; line-height: 1.3; color: var(--black); font-style: normal; white-space: nowrap; }
  .contact__name { color: var(--orange); font-weight: 700; }
  .footnote { position: absolute; left: 200px; bottom: 12px; font-size: 9px; color: var(--white); }
</style>
</head>
<body>

<section class="flyer flyer--front">
  <div class="flyer__stripe"></div>
  <div class="brand brand--front">belvo</div>
  <div class="front__panel">
    <h1 class="headline">Fahrzeugaufbereitung</h1>
    <p class="front__sub">inkl. Hol- und Bringedienst</p>
    <p class="front__text">Sparen Sie Ihre wertvolle Zeit und lassen Sie Ihr Fahrzeug von uns an Ihrem Wunschort abholen und innerhalb der nächsten 90 Minuten aufbereiten.</p>
    <p class="front__url">www.belvo-fahrdienst.de</p>
  </div>
  <div class="photo photo--front" role="img" aria-label="Foto von oben: Team in weißer Kleidung und blauen Mützen reinigt ein silbernes Cabrio"></div>
  <div class="badge badge--price">
    <svg viewBox="0 0 150 150"><circle cx="75" cy="75" r="62" fill="var(--blue)" stroke="var(--blue)" stroke-width="13" stroke-dasharray="10 9.9"/></svg>
    <div class="badge__text">
      <span class="nur">nur</span>
      <span class="price"><small>€</small>59,<sup>90*</sup></span>
    </div>
  </div>
</section>

<section class="flyer flyer--back">
  <div class="flyer__stripe"></div>
  <div class="photo photo--back" role="img" aria-label="Foto von oben: Mitarbeiter reinigen Innenraum und Motorhaube eines weißen Cabrios"></div>
  <p class="footnote">* Preise inkl. MwSt. und freibleibend</p>
  <div class="back__top">
    <h2 class="headline">Fahrzeugaufbereitung</h2>
    <p class="back__intro">Wir bieten Ihnen eine klassische Fahrzeugaufbereitung inkl. Hol- und Bringedienst in Berlin und München für nur 59,90 € * an.</p>
  </div>
  <div class="badge badge--new">
    <svg viewBox="0 0 150 150"><circle cx="75" cy="75" r="62" fill="var(--blue)" stroke="var(--blue)" stroke-width="13" stroke-dasharray="10 9.9"/></svg>
    <div class="badge__text">Ihr Auto<br>wie<span class="big">NEU</span></div>
  </div>
  <div class="services">
    <p class="services__title">Unser Leitungsangebot enthält:</p>
    <ul>
      <li>Hol- und Bringeservice</li>
      <li>Aussenwäsche inkl. Felgenreinigung</li>
      <li>Innenreinigung inkl. Cockpit und Saugen</li>
      <li>Fensterreinigung innen &amp; aussen</li>
      <li>Öl-, Wasser- und Wischwasserkontrolle</li>
      <li>Reifendruck und Profilkontrolle</li>
    </ul>
  </div>
  <p class="cta">Vereinbaren Sie noch heute einen Termin!</p>
  <address class="contact">
    <span class="contact__name">B.E.L.V.O. GmbH</span><br>
    Lindenhofstr. 27 · 10827 Berlin<br>
    Tel.: 030 55 41 27 6 -0<br>
    Mail: info@belvo-fahrdienst.de · Web: www.belvo-fahrdienst.de
  </address>
  <div class="brand brand--back">belvo</div>
</section>

</body>
</html>
```